Hair and Wellness Brochure and Pricelist design

I am requiring a brochure that has a fresh, though alternative design. My business name is The Quiet Orchard Hair and Wellness. I have a very professional approach to my work and love to give that little bit extra to all of my clients. My passion for health, has led me to channel my business alternatively by using non toxic colours and styling products and through that same vein, I have studied Aromatherapy, Indian Head Massage and Reiki...all additional services I use where required.
My studio has very neutral tones of beige,white and beech wood but these tones aren't necessarily required for the brochure.I like to create a space of calm, peace and quiet, where my clients feel refreshed and rejuvenated..

Industry/Entity Type

Business

```html
<!DOCTYPE html>
<html lang="en">
<head>
<meta charset="utf-8">
<title>The Quiet Orchard Hair and Wellness – Price List 2013 Brochure</title>
<link href="https://fonts.googleapis.com/css2?family=Barlow:wght@400;500;600;700&display=swap" rel="stylesheet">
<style>
  :root{
    --paper:#ffffff;
    --wood-light:#d9b19c;
    --wood-mid:#c99a84;
    --wood-dark:#b88672;
    --band:rgba(255,245,240,0.55);
    --green-light:#8dc63f;
    --green-dark:#5e9e3c;
    --leaf-light:#c6e07a;
    --leaf-dark:#4f8f2e;
    --ink:#231a17;
    --label:#222222;
    --fold:#6a5048;
    --skin:#e9b9a0;
    --hair:#f1dfb8;
    --icon-grey:#d9dde3;
  }
  *{margin:0;padding:0;box-sizing:border-box}
  html,body{width:1200px;height:1000px;overflow:hidden;background:var(--paper)}
  body{position:relative;font-family:"Barlow",Arial,sans-serif;color:var(--ink)}

  .panel-label{position:absolute;top:36px;width:200px;text-align:center;font-size:16px;font-weight:400;letter-spacing:.5px;color:var(--label)}
  .label-fold{left:133px}.label-back{left:499px}.label-front{left:866px}

  .sheet{position:absolute;left:50px;top:73px;width:1100px;height:854px;overflow:hidden;
    background:
      repeating-linear-gradient(90deg,rgba(255,255,255,0.05) 0 140px,rgba(120,70,50,0.06) 140px 260px),
      repeating-linear-gradient(180deg,rgba(255,255,255,0.05) 0 72px,rgba(120,70,50,0.05) 72px 74px),
      linear-gradient(180deg,var(--wood-mid),var(--wood-light) 45%,var(--wood-mid));}

  .foliage{position:absolute;border-radius:50%;filter:blur(6px)}
  .foliage-top{right:-60px;top:-80px;width:470px;height:330px;
    background:radial-gradient(ellipse at 70% 30%,var(--leaf-dark),var(--leaf-light) 55%,rgba(198,224,122,0) 72%)}
  .foliage-right{right:-80px;top:240px;width:200px;height:300px;
    background:radial-gradient(ellipse at 80% 40%,var(--leaf-light),rgba(198,224,122,0) 70%)}
  .foliage-bottom{left:-120px;bottom:-140px;width:560px;height:480px;
    background:radial-gradient(ellipse at 25% 70%,var(--leaf-dark),var(--leaf-light) 50%,rgba(198,224,122,0) 72%)}

  .band{position:absolute;left:0;top:110px;width:1100px;height:87px;background:var(--band)}

  .fold-line{position:absolute;top:0;height:854px;border-left:1.5px dashed var(--fold)}
  .fold-1{left:366px}.fold-2{left:731px}

  .ribbon{position:absolute;width:262px;height:48px}
  .ribbon svg{position:absolute;inset:0;filter:drop-shadow(0 2px 3px rgba(0,0,0,.3))}
  .ribbon span{position:relative;display:block;text-align:center;line-height:48px;color:#fff;font-weight:700;font-size:23px;letter-spacing:.5px}
  .ribbon-welcome{left:48px;top:131px}
  .ribbon-contact{left:413px;top:131px}
  .ribbon-price{left:772px;top:738px;width:280px}

  .welcome-copy{position:absolute;left:49px;top:216px;width:260px;font-size:13px;font-weight:600;line-height:18px}
  .welcome-copy p{margin-bottom:6px}

  .contact-block{position:absolute;left:366px;top:268px;width:365px;text-align:center;font-size:16px;font-weight:600;line-height:20px}
  .contact-block .business{margin-bottom:6px}
  .contact-block .social{margin-top:26px}
  .social-square{display:block;width:52px;height:52px;margin:10px auto 0;border-radius:8px;background:var(--icon-grey);box-shadow:0 1px 3px rgba(0,0,0,.3)}

  .brand-seal{position:absolute;width:210px;height:210px;border-radius:50%;
    background:linear-gradient(90deg,var(--green-light),var(--green-dark));
    display:flex;align-items:center;justify-content:center;text-align:center;
    color:#fff;font-weight:700;font-size:21px;line-height:26px;padding:0 26px;
    box-shadow:0 2px 6px rgba(0,0,0,.25)}
  .seal-back{left:439px;top:577px}
  .seal-front{left:809px;top:49px}

  .portrait{position:absolute;left:770px;top:268px;width:330px;height:586px;
    border-radius:46% 40% 0 0/28% 24% 0 0;
    background:radial-gradient(ellipse at 45% 40%,var(--skin) 0 30%,var(--hair) 55%,rgba(241,223,184,0.6) 80%)}
</style>
</head>
<body>
  <div class="panel-label label-fold">FOLD IN</div>
  <div class="panel-label label-back">BACK</div>
  <div class="panel-label label-front">FRONT</div>

  <div class="sheet">
    <div class="foliage foliage-top" role="img" aria-label="Fresh green leaves framing the top corner"></div>
    <div class="foliage foliage-right" role="img" aria-label="Green leaves along the right edge"></div>
    <div class="foliage foliage-bottom" role="img" aria-label="Green leafy branches in the lower corner"></div>

    <div class="band"></div>

    <div class="portrait" role="img" aria-label="Photograph of a woman with long blonde hair, eyes lowered, looking over her shoulder"></div>

    <div class="fold-line fold-1"></div>
    <div class="fold-line fold-2"></div>

    <div class="ribbon ribbon-welcome">
      <svg width="262" height="48" viewBox="0 0 262 48"><defs><linearGradient id="rg1" x1="0" x2="1"><stop offset="0" stop-color="#8dc63f"/><stop offset="1" stop-color="#5e9e3c"/></linearGradient></defs>
        <polygon points="0,0 262,0 254,24 262,48 0,48 8,24" fill="url(#rg1)"/>
        <line x1="12" y1="5" x2="250" y2="5" stroke="#fff" stroke-dasharray="4 3"/>
        <line x1="12" y1="43" x2="250" y2="43" stroke="#fff" stroke-dasharray="4 3"/></svg>
      <span>WELCOME</span>
    </div>

    <div class="welcome-copy">
      <p>Here at The Quiet Orchard Hair and Wellness, we specialize in all professional hairdressing services including corrective colour services and wedding up styles.</p>
      <p>Our chief stylist Mara has over 20 years experience in the industry with an education obtained at the prestigious Marlowe Styling Academy in London.</p>
      <p>With a focus on health, we pride ourselves on using non toxic colours and styling products so you’ll never have to worry about harsh chemicals damaging your hair or your skin.</p>
    </div>

    <div class="ribbon ribbon-contact">
      <svg width="262" height="48" viewBox="0 0 262 48"><defs><linearGradient id="rg2" x1="0" x2="1"><stop offset="0" stop-color="#8dc63f"/><stop offset="1" stop-color="#5e9e3c"/></linearGradient></defs>
        <polygon points="0,0 262,0 254,24 262,48 0,48 8,24" fill="url(#rg2)"/>
        <line x1="12" y1="5" x2="250" y2="5" stroke="#fff" stroke-dasharray="4 3"/>
        <line x1="12" y1="43" x2="250" y2="43" stroke="#fff" stroke-dasharray="4 3"/></svg>
      <span>CONTACT</span>
    </div>

    <div class="contact-block">
      <div class="business">The Quiet Orchard<br>Hair and Wellness</div>
      <div>Mara Ellison<br>0400 555 218<br>mara.ellison@example.com</div>
      <div class="social">LIKE US on friendbook</div>
      <span class="social-square"></span>
    </div>

    <div class="brand-seal seal-back">The Quiet Orchard Hair &amp; Wellness</div>
    <div class="brand-seal seal-front">The Quiet Orchard Hair &amp; Wellness</div>

    <div class="ribbon ribbon-price">
      <svg width="280" height="48" viewBox="0 0 280 48"><defs><linearGradient id="rg3" x1="0" x2="1"><stop offset="0" stop-color="#8dc63f"/><stop offset="1" stop-color="#5e9e3c"/></linearGradient></defs>
        <polygon points="0,0 280,0 272,24 280,48 0,48 8,24" fill="url(#rg3)"/>
        <line x1="12" y1="5" x2="268" y2="5" stroke="#fff" stroke-dasharray="4 3"/>
        <line x1="12" y1="43" x2="268" y2="43" stroke="#fff" stroke-dasharray="4 3"/></svg>
      <span>PRICE LIST 2013</span>
    </div>
  </div>
</body>
</html>
```